Quorva - corporate Business Card

We need a good look and innovative business card for a new start up company based in Los Angeles called "Quorva". We are in a payment business, including payment card, app, and ewallet. We are expert in online payment and Card not present (CNP) transaction.
We need an innovative, modern business card.

Our logo font is Aero Matics

Target Market(s)

Startup - Bank - Online Payment - Card Manufacturing

Industry/Entity Type

Startup

Contact Information for Business Card

phone: 555 014 7396 - Address: 4172 Marlowe blvd, Dunmore Vale, NV 89012

Requirements
Must have
• Message: innovative, professional, expert, high tech, trust, online payment expert, security
Nice to have
• no comment
Should not have
• no Comment

```html
<!DOCTYPE html>
<html lang="en">
<head>
<meta charset="utf-8">
<title>Quorva – Business Card</title>
<link rel="stylesheet" href="https://fonts.googleapis.com/css2?family=Open+Sans:wght@400;600;700&display=swap">
<style>
  :root {
    --brand-red: #b81f31;
    --paper: #ffffff;
    --ink: #555555;
    --stage: #e9e7e4;
    --faint: rgba(255, 255, 255, 0.12);
  }
  * { margin: 0; padding: 0; box-sizing: border-box; }
  html, body {
    width: 1200px; height: 987px; overflow: hidden;
    background: var(--stage);
    font-family: "Open Sans", Arial, sans-serif;
  }
  .card {
    position: absolute;
    left: 293px;
    width: 615px; height: 350px;
    overflow: hidden;
    box-shadow: 0 3px 10px rgba(0,0,0,0.18);
  }
  .card-front { top: 130px; background: var(--paper); }
  .card-back  { top: 506px; background: var(--brand-red); }

  /* front */
  .brand {
    position: absolute; left: 43px; top: 58px;
    display: flex; align-items: center; gap: 12px;
  }
  .brand-dot {
    width: 54px; height: 54px; border-radius: 50%;
    background: var(--brand-red);
  }
  .brand-name {
    font-size: 48px; font-weight: 600; line-height: 1;
    color: var(--brand-red); letter-spacing: 0.5px;
  }
  .address {
    position: absolute; left: 43px; top: 186px;
    font-style: normal;
    font-size: 16px; line-height: 22px; color: var(--ink);
  }
  .contact-list {
    position: absolute; left: 43px; top: 242px;
    list-style: none; font-size: 16px; line-height: 23.5px; color: var(--ink);
  }
  .contact-list li { display: flex; align-items: center; gap: 9px; }
  .contact-list svg { width: 14px; height: 14px; flex: none; }

  .name-band {
    position: absolute; left: 363px; right: 0; top: 214px; height: 72px;
    background: var(--brand-red);
  }
  .name-dot {
    position: absolute; left: 333px; top: 213px;
    width: 74px; height: 74px; border-radius: 50%;
    background: var(--brand-red);
    border: 3px solid var(--paper);
  }
  .person {
    position: absolute; right: 26px; top: 222px;
    text-align: right; color: var(--paper);
  }
  .person-name { font-size: 19px; font-weight: 700; line-height: 28px; letter-spacing: 0.2px; }
  .person-title { font-size: 16px; line-height: 22px; }

  /* back */
  .back-circle {
    position: absolute; left: 13px; top: 16px;
    width: 320px; height: 320px; border-radius: 50%;
    background: var(--faint);
  }
  .back-brand {
    position: absolute; right: 45px; top: 248px;
    text-align: right; color: var(--paper);
  }
  .back-name { font-size: 56px; font-weight: 600; line-height: 1; letter-spacing: 1px; }
  .back-url { margin-top: 6px; font-size: 14px; letter-spacing: 4.5px; }
</style>
</head>
<body>

<section class="card card-front">
  <div class="brand">
    <span class="brand-dot"></span>
    <span class="brand-name">Quorva</span>
  </div>

  <address class="address">
    4172 Marlowe blvd<br>
    Dunmore Vale, NV 89012
  </address>

  <ul class="contact-list">
    <li>
      <svg viewBox="0 0 16 16" aria-hidden="true"><path fill="var(--brand-red)" d="M3.6 1.2l2.3 2.6-1.3 2a8.5 8.5 0 0 0 5.6 5.6l2-1.3 2.6 2.3-1.6 2.4C7.8 15 1 8.2 1.2 2.8z"/></svg>
      555 014 7396
    </li>
    <li>
      <svg viewBox="0 0 16 16" aria-hidden="true"><rect x="1" y="3" width="14" height="10" fill="var(--brand-red)"/><path d="M1.5 3.5L8 9l6.5-5.5" fill="none" stroke="#fff" stroke-width="1.3"/></svg>
      dana@quorva.com
    </li>
    <li>
      <svg viewBox="0 0 16 16" aria-hidden="true"><circle cx="8" cy="8" r="7" fill="var(--brand-red)"/><path d="M1 8h14M8 1c-3 3.5-3 10.5 0 14M8 1c3 3.5 3 10.5 0 14" fill="none" stroke="#fff" stroke-width="1"/></svg>
      www.quorva.com
    </li>
  </ul>

  <div class="name-band"></div>
  <div class="name-dot"></div>
  <div class="person">
    <div class="person-name">DANA WHITFIELD</div>
    <div class="person-title">CEO&amp;Founder</div>
  </div>
</section>

<section class="card card-back">
  <div class="back-circle"></div>
  <div class="back-brand">
    <div class="back-name">Quorva</div>
    <div class="back-url">www.quorva.com</div>
  </div>
</section>

</body>
</html>
```